Hong Kong based International Remittance and ForEx company requires website design

We need a website designed for a new European - Hong Kong based ForEx & fund remittence entity.

The company specialises in larger corporate & high net worth private client trades, therefore the design must aesthetically reflect this (sophisticated). As a theme colour, financial entities tend to use either blue or red; if blue, our preference is a darker blue. Visually, our preference is less copy, more imagery.

Number of pages would be limited; landing (home), about us, client registration (x1 Corporate form, x1 Private Client form), Contact Us.

Have uploaded the existing logo - please note this is to be redesigned, although the colour scheme will remain the same. Please also note that copy will follow - please use Lorem Ipsum.

Target Market(s)

Medium to large Corporations. High net worth individuals.

Industry/Entity Type

Financial Service

Coding

Coded - Design and coding required

Number of Pages Required

4 page

Font styles to use
Serif

Requirements
Nice to have
• ForEx ticker,

```html
<!DOCTYPE html>
<html lang="en">
<head>
<meta charset="utf-8">
<title>Harbourline Incorporation Limited</title>
<link href="https://fonts.googleapis.com/css2?family=Open+Sans:ital,wght@0,400;0,600;0,700;1,400&display=swap" rel="stylesheet">
<style>
:root{
  --navy:#1f5d99;
  --nav:#2a6fb2;
  --nav-dark:#2b1f1c;
  --band:#2468a8;
  --about:#1c4f83;
  --ink:#333;
  --muted:#666;
  --link:#1f6eb4;
  --up:#2aa52a;
  --down:#e02c2c;
  --footer:#251b18;
  --white:#fff;
}
*{margin:0;padding:0;box-sizing:border-box}
html,body{width:1200px;height:2466px;overflow:hidden;background:#fff}
body{font-family:"Open Sans",Arial,sans-serif;color:var(--ink);position:relative}
.page{position:relative;width:1200px;height:2466px;overflow:hidden}
.abs{position:absolute}

/* header */
.brand{left:99px;top:40px;display:flex;align-items:center;gap:14px}
.brand-mark{width:46px;height:46px;border-radius:50%;background:#c9d6e6}
.brand-name{font-size:30px;font-weight:600;color:#2a2a2a;line-height:1.1}
.brand-sub{font-size:10px;letter-spacing:3px;color:#2a2a2a;font-weight:600;margin-top:4px}
.contact{top:44px;display:flex;gap:12px;font-size:13px;color:#444}
.contact .label{font-size:12px;margin-bottom:8px}
.contact .value{font-size:15px}
.contact .addr{font-size:12px;line-height:26px}

/* nav */
.nav{left:0;top:158px;width:1200px;height:56px;background:linear-gradient(#2f78bc,#2466a6);border-top:3px solid #3d86c8}
.nav ul{list-style:none;display:flex;position:absolute;left:99px;top:0;height:53px}
.nav li{color:#fff;font-size:12px;height:53px;line-height:53px;text-transform:uppercase}
.nav .active{background:var(--nav-dark);width:136px;text-align:center}
.dropdown{left:500px;top:225px;width:212px;background:#fff;box-shadow:0 2px 6px rgba(0,0,0,.25);z-index:3}
.dropdown div{font-size:11px;color:#444;height:26px;line-height:26px;padding-left:14px;border-bottom:1px solid #e6e6e6}

/* hero */
.hero{left:0;top:214px;width:1200px;height:513px;background:linear-gradient(120deg,#5d93b6 0%,#2e5a86 45%,#24466e 70%,#3b5f86 100%)}
.hero-caption{left:99px;top:407px;width:335px;height:121px;background:rgba(30,30,30,.8);color:#fff;text-align:center;padding-top:22px}
.hero-caption .t1{font-size:28px;font-weight:700}
.hero-caption .t2{font-size:28px;font-weight:400}
.hero-arrows{left:1042px;top:640px;display:flex;gap:8px}

/* ticker */
.ticker-band{left:0;top:727px;width:1200px;height:85px;background:var(--band);border-bottom:4px solid #1d3f66}
.ticker{left:99px;top:753px;width:1002px;height:36px;background:#fff;border-radius:4px;display:flex;align-items:center;gap:22px;padding:0 14px;font-size:11px;color:var(--link);white-space:nowrap;overflow:hidden}
.up{color:var(--up)} .down{color:var(--down)}

/* section titles */
.section-title{display:flex;align-items:center;justify-content:center;gap:18px;width:1200px;left:0;font-size:29px;color:#333}
.section-icon{width:68px;height:68px;border-radius:50%;background:#cdd9e8}

/* features */
.tile{color:#fff;font-weight:600;font-size:14px;display:flex;align-items:center;justify-content:center;text-align:center}
.tile-big{left:99px;top:957px;width:506px;height:370px;background:linear-gradient(#eef2f6 0%,#cbd6e1 70%,#4f83b6 100%)}
.tile-big .cap{position:absolute;left:0;bottom:0;width:100%;height:95px;background:rgba(40,110,180,.85);padding:12px 20px;text-align:left}
.tile-big .cap h3{font-size:14px;font-weight:600;margin-bottom:8px}
.tile-big .cap p{font-size:11px;font-weight:400;line-height:18px}

/* about */
.about{left:0;top:1378px;width:1200px;height:315px;background:linear-gradient(#2a5f95,#1a4a7c)}
.about-text{left:230px;top:1512px;width:740px;text-align:center;font-style:italic;font-size:12px;color:#fff;line-height:28px}
.btn{background:linear-gradient(#2f7cc4,#1d5f9e);color:#fff;font-size:14px;font-weight:600;text-align:center;border-radius:3px;box-shadow:0 2px 3px rgba(0,0,0,.3)}

/* blog */
.post{top:1833px;width:242px}
.post .img{height:156px}
.post h4{font-size:14px;font-weight:600;color:#333;text-align:center;margin-top:14px}
.post time{display:block;font-size:11px;font-style:italic;color:var(--link);text-align:center;margin-top:4px}

/* registration */
.register{left:0;top:2085px;width:1200px;height:294px;background:linear-gradient(#c8d6e4,#eef1f4 60%,#c9d3dc)}
.register-text{left:210px;top:2210px;width:780px;text-align:center;font-size:12px;color:#444;line-height:30px}

/* footer */
.footer{left:0;top:2379px;width:1200px;height:87px;background:var(--footer);color:#fff}
.footer-links{left:166px;top:2398px;font-size:10px;word-spacing:2px}
.footer-copy{left:166px;top:2422px;font-size:10px}
.social{left:868px;top:2407px;display:flex;align-items:center;gap:8px;font-size:10px}
.social span.c{width:27px;height:27px;border:1.5px solid #fff;border-radius:50%;display:inline-block}
</style>
</head>
<body>
<div class="page">

  <header>
    <div class="abs brand">
      <span class="brand-mark"></span>
      <div>
        <div class="brand-name">Harbourline</div>
        <div class="brand-sub">INCORPORATION LIMITED</div>
      </div>
    </div>
    <div class="abs contact" style="left:570px">
      <svg width="22" height="34" viewBox="0 0 22 34"><rect x="2" y="1" width="18" height="32" rx="3" fill="#1f6eb4"/><rect x="5" y="5" width="12" height="20" fill="#fff"/><circle cx="11" cy="29" r="1.8" fill="#fff"/></svg>
      <div><div class="label">Phone:</div><div class="value">020 3157 2260</div></div>
    </div>
    <div class="abs contact" style="left:752px">
      <svg width="26" height="36" viewBox="0 0 26 36"><path d="M13 1C6 1 1 6 1 13c0 9 12 22 12 22s12-13 12-22C25 6 20 1 13 1z" fill="#1f6eb4"/><circle cx="13" cy="13" r="5" fill="#fff"/></svg>
      <div><div class="label">Location:</div><div class="addr">harbourlineincorporation,Harbourline Incorporation Limited<br>41 Harbour Terrace Central Hong Kong SAR</div></div>
    </div>
  </header>

  <nav class="abs nav">
    <ul>
      <li class="active">Home</li>
      <li style="width:170px;text-align:right">About Us &nbsp;&#8964;</li>
      <li style="width:260px;text-align:right">International Payments &nbsp;&#8964;</li>
      <li style="width:294px;text-align:right">Client Application &nbsp;&#8964;</li>
      <li style="width:180px;text-align:right">Contact Us</li>
    </ul>
  </nav>
  <div class="abs dropdown">
    <div>&rsaquo; Making Payments</div>
    <div>&rsaquo; Customer Protection</div>
    <div>&rsaquo; No Obligation</div>
    <div>&rsaquo; Corporate Clients</div>
    <div style="border:0">&rsaquo; Private Clients</div>
  </div>

  <section class="abs hero" role="img" aria-label="Hand holding a smartphone with glowing finance icons floating above it"></section>
  <div class="abs hero-caption"><div class="t1">NEW FOREX &amp; FUND</div><div class="t2">REMITTANCE..!</div></div>
  <div class="abs hero-arrows">
    <svg width="26" height="26"><circle cx="13" cy="13" r="12" fill="rgba(255,255,255,.5)"/><path d="M15 7l-6 6 6 6" stroke="#444" stroke-width="2" fill="none"/></svg>
    <svg width="26" height="26"><circle cx="13" cy="13" r="12" fill="rgba(255,255,255,.5)"/><path d="M11 7l6 6-6 6" stroke="#444" stroke-width="2" fill="none"/></svg>
  </div>

  <div class="abs ticker-band"></div>
  <div class="abs ticker">
    <span>&#9664;&#9664;</span>
    <span>GLOBAL TRADE CORP GTC 80.70 <span class="up">&#9660;0.77 &#9660;0.88%</span></span>
    <span>GLOBAL TRADE CORP GTC 80.70 <span class="down">&#9650;0.77 &#9650;0.88%</span></span>
    <span>GLOBAL TRADE CORP GTC 80.70 <span class="up">&#9660;0.77 &#9660;0.88%</span></span>
    <span>GLOBAL TRADE CORP GTC 80.70 <span class="down">&#9650;0.77 &#9650;0.88%</span></span>
    <span>&#9654;&#9654;</span>
  </div>

  <h2 class="abs section-title" style="top:858px"><span class="section-icon"></span>Our Features</h2>
  <div class="abs tile tile-big" role="img" aria-label="Two hands exchanging a banknote through a smartphone in front of a city skyline">
    <div class="cap"><h3>International Money Transfer</h3><p>Sed ut perspiciatis unde omnis iste natus error sit voluptatem accusantium doloremque laudantium, totam rem aperiam, eaque ipsa quae ab...</p></div>
  </div>
  <div class="abs tile" style="left:618px;top:957px;width:235px;height:177px;background:linear-gradient(#2f6fa8,#1d4f80)" role="img" aria-label="Stacks of coins over a currency chart">Foreign Exchange</div>
  <div class="abs tile" style="left:866px;top:957px;width:235px;height:177px;background:linear-gradient(#3a76ad,#24558a)" role="img" aria-label="Businessman holding a glowing growth chart">Paying &amp; Receiving Agency</div>
  <div class="abs tile" style="left:618px;top:1148px;width:235px;height:179px;background:linear-gradient(#2b6aa6,#163f6c)" role="img" aria-label="Blue stock market chart">Praesentium voluptatum</div>
  <div class="abs tile" style="left:866px;top:1148px;width:235px;height:179px;background:linear-gradient(#5e8fb8,#2f5f8e)" role="img" aria-label="Businessman looking out of an office window">Deleniti atque corrupti</div>

  <section class="abs about" role="img" aria-label="Blue tinted city skyline"></section>
  <h2 class="abs section-title" style="top:1422px;color:#fff"><span class="section-icon" style="background:#dfe8f2"></span>About Us</h2>
  <p class="abs about-text">Harbourline is a leading provider of international payment services and foreign exchange to corporations and individuals covering most of the world including;&nbsp; throughout Asia, South America, and Europe...</p>
  <div class="abs btn" style="left:503px;top:1588px;width:196px;height:52px;line-height:52px">Click Read More Info</div>

  <h2 class="abs section-title" style="top:1730px"><span class="section-icon"></span>Latest blog</h2>
  <article class="abs post" style="left:99px"><div class="img" role="img" aria-label="Businessman holding a tablet over a city" style="background:linear-gradient(#8ea4b8,#5d6f80)"></div><h4>Accusantium doloremqu</h4><time>Posted on 28 February 2016</time></article>
  <article class="abs post" style="left:353px"><div class="img" role="img" aria-label="Modern city skyline under blue sky" style="background:linear-gradient(#5f9ad6,#c4d6e2)"></div><h4>Accusantium doloremqu</h4><time>Posted on 28 February 2016</time></article>
  <article class="abs post" style="left:607px"><div class="img" role="img" aria-label="Businessman touching a digital finance screen" style="background:linear-gradient(#1f3f66,#0d1f36)"></div><h4>Accusantium doloremqu</h4><time>Posted on 28 February 2016</time></article>
  <article class="abs post" style="left:860px"><div class="img" role="img" aria-label="Business people working at a desk with a laptop" style="background:linear-gradient(#b8a99a,#7c6d60)"></div><h4>Accusantium doloremqu</h4><time>Posted on 28 February 2016</time></article>

  <section class="abs register" role="img" aria-label="Pale city skyline reflected in water"></section>
  <h2 class="abs section-title" style="top:2122px;color:#2a78c0"><span class="section-icon" style="background:#e4ebf3"></span>Client Registration</h2>
  <p class="abs register-text">Coupled with our excellent customer service, highly competitive rates and in depth market knowledge we provide a simple, reliable and cost effective service to all of our clients.</p>
  <div class="abs btn" style="left:503px;top:2287px;width:196px;height:52px;line-height:52px">Click to Register</div>

  <footer class="abs footer"></footer>
  <span class="abs" style="left:99px;top:2400px;width:46px;height:46px;border-radius:50%;background:#c9d6e6"></span>
  <div class="abs footer-links" style="color:#fff">HOME &nbsp;| &nbsp;ABOUT US &nbsp;| &nbsp;INTERNATIONAL PAYMENTS &nbsp;| &nbsp;CLIENT APPLICATION &nbsp;| &nbsp;CONTACT US</div>
  <div class="abs footer-copy" style="color:#fff">COPYRIGHTS&copy;HARBOURLINEINCORPORATION.2016 | ALLRIGHTS RESERVED.</div>
  <div class="abs social" style="color:#fff">CONNECT WITH US: &nbsp;<span class="c"></span><span class="c"></span><span class="c"></span><span class="c"></span></div>

</div>
</body>
</html>
```